Transform Your Giving

I need a tri-fold brochure that will fit in a standard number 10 business envelope. Meadowlark and Allied Services is a charitable nonprofit. The goal of this brochure is to stimulate people into thinking about other ways to make a donation. The design should communicate the essential information on donation options, create a sense of professional integrity, be graphically sharp, easy to read and laid out in a way that doesn't make the material appear crowded.

```html
<!DOCTYPE html>
<html lang="en">
<head>
<meta charset="utf-8">
<title>Transform Your Giving – Meadowlark and Allied Services</title>
<link href="https://fonts.googleapis.com/css2?family=Poppins:ital,wght@0,400;0,500;0,600;0,700;1,400&family=Rubik:wght@500;600;700&display=swap" rel="stylesheet">
<style>
  :root{
    --navy:#2b2a72;
    --green:#3db54a;
    --ink:#3a3a44;
    --white:#ffffff;
    --paper:#ffffff;
    --gold:#f5b914;
  }
  *{box-sizing:border-box;margin:0;padding:0}
  html,body{width:728px;height:1200px;overflow:hidden;background:var(--paper)}
  body{font-family:"Poppins",sans-serif;color:var(--ink)}
  .sheet{position:relative;width:1500px;height:2472px;transform:scale(.485333);transform-origin:0 0}
  .spread{position:absolute;left:85px;width:1325px;height:1025px;box-shadow:0 6px 14px rgba(0,0,0,.18);overflow:hidden;background:var(--white)}
  .spread--outside{top:100px}
  .spread--inside{top:1225px}
  .panel{position:absolute;top:0;height:1025px;overflow:hidden}
  .panel--a{left:0;width:435px}
  .panel--b{left:435px;width:445px}
  .panel--c{left:880px;width:445px}
  .fold-shade{position:absolute;top:0;left:0;width:70px;height:100%;background:linear-gradient(90deg,rgba(0,0,0,.10),rgba(0,0,0,0));pointer-events:none}
  .abs{position:absolute}
  .bg{position:absolute;left:0;top:0}
  .photo{position:absolute;border-radius:50%;border:7px solid var(--white)}
  .heading{font-family:"Rubik",sans-serif;font-weight:600;line-height:1.08;white-space:nowrap}
  .navy{color:var(--navy)}
  .green{color:var(--green)}
  .white{color:var(--white)}
  .body-copy{font-size:15px;line-height:1.22}
  .small-copy{font-size:13.5px;line-height:1.2}
  .center{text-align:center}
  .pill{position:absolute;background:var(--green);color:var(--white);font-weight:700;text-align:center;border-radius:6px;white-space:nowrap}
  .how{font-family:"Rubik",sans-serif;font-weight:600;font-size:20px;color:var(--navy)}
  .how span{color:var(--green)}
  .gift-list{list-style:none;font-size:16px;font-weight:600;color:var(--ink)}
  .gift-list li{position:relative;padding:0 0 10px 27px;margin-bottom:10px;border-bottom:1px dotted #9a9a9a;width:290px}
  .gift-list li:last-child{border-bottom:none}
  .gift-list li::before{content:"";position:absolute;left:0;top:6px;width:10px;height:10px;border-radius:50%;background:var(--green)}
  .contact-icon{position:absolute;width:36px;height:36px;border-radius:50%;background:var(--navy)}
  .option-icon{position:absolute;width:60px;height:60px;border-radius:50%;background:var(--navy)}
  .option-label{position:absolute;width:110px;text-align:center;font-weight:700;font-size:15px;line-height:1.2;color:var(--ink)}
  .bullets{list-style:none}
  .bullets li{position:relative;padding-left:18px;margin-bottom:14px}
  .bullets li::before{content:"";position:absolute;left:0;top:7px;width:6px;height:6px;border-radius:50%;background:var(--green)}
</style>
</head>
<body>
<main class="sheet">

  <section class="spread spread--outside">

    <div class="panel panel--a">
      <svg class="bg" width="435" height="1025" viewBox="0 0 435 1025">
        <rect width="435" height="1025" fill="#ffffff"/>
        <path d="M295 0 H435 V640 C400 500 385 320 350 200 C330 120 312 55 295 0 Z" fill="#2b2a72"/>
        <path d="M295 0 C312 55 330 120 350 200 C385 320 400 500 435 640" stroke="#3db54a" stroke-width="6" fill="none"/>
        <ellipse cx="160" cy="40" rx="200" ry="150" fill="#3db54a"/>
        <path d="M250 1025 C340 950 410 870 435 800" stroke="#3db54a" stroke-width="5" fill="none"/>
      </svg>
      <div class="photo" role="img" aria-label="Photo: a smiling couple packing donated clothes into a box" style="left:-10px;top:78px;width:360px;height:360px;background:linear-gradient(150deg,#e9d9c6,#7a9bc2 55%,#c98c62)"></div>

      <h2 class="heading abs navy" style="left:47px;top:492px;font-size:24px;font-weight:700">THE IMPACT <span class="green">OF YOUR GIFT</span></h2>
      <p class="body-copy abs" style="left:47px;top:530px;width:335px">Your generosity drives our mission. With every Smart gift you’re supporting Meadowlark and Allied Services. Join our community of Smart Givers today and make an enduring impact. With Smart Giving your generosity reaches further. Begin your Smart Giving journey with us today.</p>
      <ul class="gift-list abs" style="left:47px;top:692px">
        <li>Stocks and Securities</li>
        <li>DAFs</li>
        <li>QCDs</li>
        <li>Crypto</li>
        <li>Charitable Annuity</li>
      </ul>
      <div class="pill" style="left:47px;top:920px;width:290px;height:38px;font-size:16px;line-height:38px">www.meadowlarkallied.org</div>
    </div>

    <div class="panel panel--b">
      <svg class="bg" width="445" height="1025" viewBox="0 0 445 1025">
        <rect width="445" height="1025" fill="#2b2a72"/>
        <path d="M0 520 C60 440 150 415 225 415 C300 415 390 440 445 520 V1025 H0 Z" fill="#3db54a"/>
        <path d="M0 545 C60 460 150 432 225 432 C300 432 390 460 445 545 V1025 H0 Z" fill="#ffffff"/>
      </svg>
      <div class="fold-shade"></div>
      <p class="body-copy white center abs" style="left:45px;top:52px;width:355px">To learn more about Smart Giving Options and how they can benefit you and Meadowlark and Allied Services, please reach out to our team. We’re here to help you navigate these giving methods and answer any question you may have.</p>
      <p class="body-copy white center abs" style="left:45px;top:178px;width:355px;font-style:italic">Being kind to others is a way of being good to yourself.<br><span class="green">Ruth Ellison</span></p>
      <p class="white center abs" style="left:0;top:270px;width:445px;font-size:18px">If you do not have a will, go to</p>
      <div class="pill" style="left:82px;top:300px;width:282px;height:32px;font-size:21px;line-height:32px;border-radius:8px">www.OpenWillNow.org</div>
      <p class="white center abs" style="left:0;top:338px;width:445px;font-size:17px;line-height:1.2">In 20 minutes you can have a<br>legal will – FOR FREE.</p>

      <h2 class="abs center" style="left:0;top:468px;width:445px;font-size:23px;font-weight:700;color:#111">CONTACT US</h2>
      <p class="abs center green" style="left:0;top:494px;width:445px;font-size:18px;font-weight:700">Have more question?</p>
      <p class="abs center" style="left:0;top:516px;width:445px;font-size:14px;line-height:1.2;color:#111">Please contact us at Meadowlark and<br>Allied Services</p>

      <div class="contact-icon" style="left:204px;top:557px"></div>
      <svg class="abs" style="left:211px;top:564px" width="22" height="22" viewBox="0 0 24 24"><path d="M6.6 10.8a15 15 0 0 0 6.6 6.6l2.2-2.2c.3-.3.7-.4 1-.2 1.1.4 2.3.6 3.6.6.6 0 1 .4 1 1V20c0 .6-.4 1-1 1A17 17 0 0 1 3 4c0-.6.4-1 1-1h3.5c.6 0 1 .4 1 1 0 1.3.2 2.5.6 3.6.1.3 0 .7-.2 1z" fill="#3db54a"/></svg>
      <p class="abs center" style="left:0;top:594px;width:445px;font-size:17px;font-weight:700;color:#111">555-014-2200 (ext. 100)</p>

      <div class="contact-icon" style="left:204px;top:621px"></div>
      <svg class="abs" style="left:212px;top:630px" width="20" height="18" viewBox="0 0 20 16"><rect x="1" y="1" width="18" height="14" rx="2" fill="#3db54a"/><path d="M1 2 L10 9 L19 2" stroke="#2b2a72" stroke-width="1.6" fill="none"/></svg>
      <p class="abs center" style="left:0;top:660px;width:445px;font-size:12px;color:#111">giving@meadowlarkallied.org</p>

      <div class="contact-icon" style="left:204px;top:679px"></div>
      <svg class="abs" style="left:213px;top:686px" width="18" height="22" viewBox="0 0 18 22"><path d="M9 1a7 7 0 0 0-7 7c0 5 7 13 7 13s7-8 7-13a7 7 0 0 0-7-7z" fill="#3db54a"/><circle cx="9" cy="8" r="2.6" fill="#2b2a72"/></svg>
      <p class="abs center" style="left:0;top:719px;width:445px;font-size:12px;line-height:1.25;color:#111">1420 Prairie View Rd. Suite 2<br>Fairhaven, ND 58000</p>

      <div class="pill" style="left:92px;top:766px;width:260px;height:28px;font-size:14px;line-height:28px">&#9678; www.meadowlarkallied.org</div>
      <p class="abs" style="left:60px;top:822px;font-size:12px;color:#111">Follow us:</p>
      <div class="abs" style="left:138px;top:834px;width:245px;border-top:1.5px dashed #555"></div>
      <p class="small-copy abs center" style="left:55px;top:858px;width:340px;color:#111">This material has been prepared for informational purposes only and is not intended to provide tax, accounting, or legal advice. Meadowlark and Allied Services is not a professional fiduciary organization. Please consult with your tax advisor or financial professional before making a decision about Smart Giving.</p>
    </div>

    <div class="panel panel--c">
      <svg class="bg" width="445" height="1025" viewBox="0 0 445 1025">
        <rect width="445" height="1025" fill="#2b2a72"/>
        <path d="M0 640 C30 520 120 450 225 450 C330 450 420 500 445 560 V1025 H0 Z" fill="#3db54a"/>
        <path d="M0 670 C30 545 120 470 225 470 C330 470 420 520 445 590 V1025 H0 Z" fill="#ffffff"/>
      </svg>
      <div class="fold-shade"></div>
      <h1 class="abs center white" style="left:0;top:45px;width:445px;font-family:'Rubik',sans-serif;font-weight:700;line-height:1;">
        <span style="display:block;font-size:32px">TRANSFORM</span>
        <span class="green" style="display:block;font-size:32px">YOUR GIVING</span>
        <span style="display:block;font-size:42px;margin-top:3px">BE STRATEGIC</span>
        <span style="display:block;font-size:42px">BE SMART</span>
      </h1>
      <p class="abs center white" style="left:0;top:208px;width:445px;font-size:21px;line-height:1.12">Discover the impact of Smart<br>Giving with Meadowlark and<br>Allied Services</p>
      <div class="photo" role="img" aria-label="Photo: an older couple embracing, seen from behind, looking at a misty landscape" style="left:62px;top:312px;width:320px;height:320px;background:linear-gradient(180deg,#c5d2de,#6f88a8 50%,#33507a)"></div>

      <div class="option-icon" style="left:100px;top:643px"></div>
      <div class="abs" style="left:111px;top:654px;width:38px;height:38px;border-radius:50%;background:var(--gold)"></div>
      <div class="option-icon" style="left:185px;top:643px"></div>
      <svg class="abs" style="left:200px;top:656px" width="30" height="32" viewBox="0 0 30 32"><path d="M2 10 L15 2 L28 10 Z" fill="#fff"/><rect x="4" y="12" width="3" height="14" fill="#fff"/><rect x="11" y="12" width="3" height="14" fill="#fff"/><rect x="17" y="12" width="3" height="14" fill="#fff"/><rect x="23" y="12" width="3" height="14" fill="#fff"/><rect x="2" y="27" width="26" height="3" fill="#fff"/></svg>
      <div class="option-icon" style="left:270px;top:643px"></div>
      <svg class="abs" style="left:283px;top:656px" width="34" height="32" viewBox="0 0 34 32"><rect x="3" y="20" width="4" height="10" fill="#39b6e8"/><rect x="10" y="16" width="4" height="14" fill="#39b6e8"/><rect x="17" y="18" width="4" height="12" fill="#39b6e8"/><rect x="24" y="12" width="4" height="18" fill="#39b6e8"/><path d="M2 16 L12 9 L18 12 L30 3" stroke="#3db54a" stroke-width="2.5" fill="none"/></svg>
      <p class="option-label" style="left:75px;top:708px">Crypto</p>
      <p class="option-label" style="left:160px;top:708px">DAF’s</p>
      <p class="option-label" style="left:245px;top:708px">Stocks &amp;<br>Securities</p>

      <div class="option-icon" style="left:97px;top:765px"></div>
      <svg class="abs" style="left:112px;top:777px" width="30" height="34" viewBox="0 0 30 34"><rect x="3" y="12" width="24" height="20" fill="#f5b914"/><rect x="13" y="10" width="4" height="22" fill="#e53935"/><rect x="1" y="9" width="28" height="5" fill="#e53935"/></svg>
      <div class="option-icon" style="left:180px;top:765px"></div>
      <svg class="abs" style="left:193px;top:777px" width="34" height="34" viewBox="0 0 34 34"><rect x="8" y="20" width="12" height="12" rx="2" fill="#f5b914"/><path d="M4 18 L14 10 L20 14 L30 4" stroke="#3db54a" stroke-width="2.5" fill="none"/></svg>
      <div class="option-icon" style="left:264px;top:765px"></div>
      <svg class="abs" style="left:278px;top:777px" width="32" height="34" viewBox="0 0 32 34"><rect x="3" y="12" width="26" height="20" rx="2" fill="#39b6e8"/><rect x="11" y="16" width="10" height="10" rx="2" fill="#f28b8b"/><rect x="12" y="2" width="10" height="8" fill="#3db54a"/></svg>
      <p class="option-label" style="left:72px;top:830px">QCDs</p>
      <p class="option-label" style="left:155px;top:830px">DAFs</p>
      <p class="option-label" style="left:239px;top:830px">Charitable<br>Annuity</p>

      <p class="abs center navy" style="left:0;top:900px;width:445px;font-size:40px;font-weight:700;line-height:1">MEADOWLARK</p>
      <p class="abs center navy" style="left:0;top:945px;width:445px;font-size:12px;font-weight:700;letter-spacing:.5px">AND ALLIED SERVICES, INC.</p>
    </div>
  </section>

  <section class="spread spread--inside">

    <div class="panel panel--a">
      <p class="body-copy abs" style="left:47px;top:47px;width:355px;font-size:15.5px">We would like to introduce you to five Strategic and Smart ways to give that could potentially be more beneficial to you compared to traditional cash donations. We encourage you to keep this information as a guide for your future contributions.</p>
      <h2 class="heading abs navy" style="left:47px;top:174px;font-size:24px">Gifts of Stocks or Appreciated<br><span class="green">Assets Strategic &amp; Smart</span></h2>
      <svg class="abs" style="left:43px;top:245px" width="92" height="80" viewBox="0 0 92 80"><rect x="2" y="46" width="12" height="32" fill="#2b2a72"/><rect x="26" y="56" width="12" height="22" fill="#2b2a72"/><rect x="50" y="44" width="12" height="34" fill="#2b2a72"/><rect x="74" y="32" width="12" height="46" fill="#2b2a72"/><path d="M2 34 L26 18 L44 34 L82 6" stroke="#3db54a" stroke-width="8" fill="none"/><path d="M70 2 L90 2 L88 20 Z" fill="#3db54a"/></svg>
      <p class="abs navy" style="left:147px;top:255px;width:235px;font-size:16px;line-height:1.15;font-weight:500"><b style="font-weight:700">Consider your long-</b><br>term publicly traded stock as a way to give to your favorite charity</p>
      <p class="small-copy abs" style="left:47px;top:347px;width:345px;font-size:14px">You can make a significantly bigger impact when you donate long-term appreciated securities, including stock, mutual funds, and bonds, directly to your favorite charity.</p>
      <p class="how abs" style="left:47px;top:432px">How Does <span>It Work?</span></p>
      <p class="body-copy abs" style="left:47px;top:467px;width:355px;font-size:15.5px">When you donate stock to a charity, you will generally take a tax deduction for the full market value. Because you are donating stock, your contribution and tax deduction may be significantly higher than contributing the after-tax proceeds. The same benefits apply when you donate mutual funds or bonds.</p>
      <svg class="bg" style="top:630px" width="445" height="395" viewBox="0 0 445 395">
        <path d="M0 150 C30 60 120 5 230 5 C330 5 410 50 445 110 V395 H0 Z" fill="#3db54a"/>
      </svg>
      <div class="abs" role="img" aria-label="Photo: a volunteer in a striped shirt sorting donated food into boxes" style="left:0;top:645px;width:445px;height:380px;border-radius:230px 230px 0 0 / 140px 140px 0 0;background:linear-gradient(160deg,#d9e2ec,#8ea6c4 45%,#b99c7c)"></div>
    </div>

    <div class="panel panel--b">
      <div class="fold-shade"></div>
      <h2 class="heading abs navy" style="left:58px;top:45px;font-size:26px">Donor-Advised Fund (DAF)<br><span class="green">Strategic &amp; Smart</span></h2>
      <div class="abs" role="img" aria-label="Illustration: a bank building with a green roof and a tax badge" style="left:58px;top:108px;width:128px;height:112px;border-radius:6px;background:linear-gradient(180deg,#3db54a 0 40%,#2b2a72 40%)"></div>
      <p class="abs navy" style="left:205px;top:123px;width:200px;font-size:15.5px;line-height:1.18;font-weight:700">Consider a DAF –<br><span style="color:#222">a simple, flexible, and tax-advantageous way to give to your favorite charities.</span></p>
      <p class="small-copy abs" style="left:56px;top:230px;width:345px;font-size:14px">A Donor-Advised Fund (DAF), is like a charitable investment account for the sole purpose of supporting your favorite charities.</p>
      <p class="how abs" style="left:56px;top:283px">How Does <span>It Work?</span></p>
      <p class="body-copy abs" style="left:56px;top:316px;width:355px;font-size:14.8px">You establish a DAF and contribute cash, stocks, or non-publicly traded assets, cryptocurrency, and private company stock to be eligible for an immediate tax deduction. Those funds are contributed for tax-free growth. You can recommend grants be made from your DAF to any IRS qualified public charity.</p>

      <svg class="bg" style="top:450px" width="445" height="200" viewBox="0 0 445 200">
        <path d="M5 190 C30 90 130 20 240 15 C340 10 420 60 440 150" stroke="#3db54a" stroke-width="10" fill="none"/>
      </svg>
      <svg class="abs" style="left:76px;top:510px" width="60" height="66" viewBox="0 0 60 66"><rect x="6" y="24" width="48" height="40" fill="#f5b914"/><rect x="26" y="20" width="8" height="44" fill="#e53935"/><rect x="2" y="18" width="56" height="9" fill="#e53935"/><path d="M30 18 C20 2 8 6 14 16 M30 18 C40 2 52 6 46 16" stroke="#e53935" stroke-width="4" fill="none"/></svg>
      <h2 class="heading abs" style="left:152px;top:483px;font-size:27px;line-height:1.12"><span class="green">Qualified<br>Charitable</span><br><span class="navy">Distributions<br>(QCDs)</span></h2>
      <p class="abs" style="left:54px;top:610px;width:360px;font-size:17px;line-height:1.1;color:#111">Consider a QCD –<br><b style="font-size:13.5px;font-weight:700">when planning your IRA withdrawal strategy… and donate to your favorite charity.</b></p>
      <p class="small-copy abs" style="left:54px;top:665px;width:360px">IRA owners at age 70 ½ or over can transfer dollars from their IRA to charity tax-free each year. These transfers known as Qualified Charitable Distributions (QCDs) offer eligible older Americans a great way to easily give to charity.</p>
      <p class="how abs" style="left:54px;top:765px">How Does <span>It Work?</span></p>
      <p class="small-copy abs" style="left:54px;top:795px;width:355px;font-size:13.2px">Are you 72 and required to take a minimum distribution (RMD) from your IRA but do not need the funds? Consider a Qualified Charitable Distribution. Normally, distributions from a traditional IRA are taxable when received. With a QCD, these distributions become tax-free when paid directly from the IRA to your favorite eligible charity. An IRA owner wishing to make a QCD should contact their IRA trustee, allowing time to complete the transaction before the end of the year to receive the tax benefit.</p>
    </div>

    <div class="panel panel--c">
      <div class="fold-shade"></div>
      <svg class="bg" width="445" height="1025" viewBox="0 0 445 1025">
        <path d="M62 0 C20 120 0 300 5 620 L0 620 C-5 300 10 120 42 0 Z" fill="#3db54a"/>
      </svg>
      <div class="abs" style="left:60px;top:45px;width:56px;height:56px;border-radius:50%;background:var(--gold);box-shadow:inset 0 0 0 5px #f9cf4a"></div>
      <h2 class="heading abs green" style="left:132px;top:50px;font-size:25px;font-weight:700">CRYPTOCURRENCY</h2>
      <p class="abs navy" style="left:132px;top:80px;font-size:17px;font-weight:500">Strategic &amp; Smart</p>
      <p class="abs" style="left:50px;top:113px;width:360px;font-size:15.5px;font-weight:600;line-height:1.15;color:#222">Consider donating Bitcoin and other cryptocurrencies to your favorite charity.</p>
      <p class="small-copy abs" style="left:45px;top:160px;width:365px">Bitcoin and other cryptocurrencies can be donated to charity just like other appreciated assets such as stocks and other business interests. Before you sell bitcoin and donate the after-tax proceeds, consider donating your bitcoin directly to a favorite charity.</p>
      <p class="how abs" style="left:45px;top:258px">How Does <span>It Work?</span></p>
      <p class="body-copy abs" style="left:48px;top:303px;width:330px;font-size:15.5px">Many donors find it useful to open a Donor-Advised Fund (DAF). This strategy</p>
      <ul class="bullets body-copy abs" style="left:48px;top:353px;width:360px;font-size:15.5px">
        <li>Your tax deduction will be equal to the fair market value of the donated bitcoin (as determined by a qualified appraisal).</li>
        <li style="margin-top:20px">Your cryptocurrency donation is tax-smart because it may eliminate capital gains taxes on the value / appreciation AND your favorite charity will receive 100% of the value of the contribution.</li>
      </ul>
      <p class="body-copy abs" style="left:50px;top:545px;width:360px;font-size:15.5px;text-align:justify">Often charities are not able to accept direct donations of bitcoin/crypto so using a DAF is a great way to donate these assets.</p>

      <svg class="abs" style="left:46px;top:612px" width="50" height="56" viewBox="0 0 50 56"><rect x="3" y="20" width="44" height="34" rx="3" fill="#39b6e8"/><rect x="3" y="20" width="44" height="8" fill="#2b8fc0"/><rect x="17" y="32" width="16" height="14" rx="3" fill="#f28b8b"/><rect x="20" y="2" width="16" height="14" fill="#3db54a" transform="rotate(20 28 9)"/></svg>
      <h2 class="heading abs green" style="left:105px;top:617px;font-size:26px;font-weight:700;line-height:1">CHARITABLE GIFT<br>ANNUITY</h2>
      <p class="abs navy" style="left:107px;top:670px;font-size:17px;font-weight:500">Strategic &amp; Smart</p>
      <p class="abs" style="left:46px;top:698px;font-size:15.5px;font-weight:600;color:#222">Consider establishing a Charitable Gift Annuity</p>
      <p class="small-copy abs" style="left:46px;top:723px;width:360px">You make a donation to a single charity. The gift is set aside in a reserve account and invested.</p>
      <p class="how abs" style="left:45px;top:762px">How Does <span>It Work?</span></p>
      <p class="body-copy abs" style="left:46px;top:795px;width:360px;font-size:15.5px;text-align:justify">A charitable gift annuity is a contract between a donor and a charity. As a donor, you make a sizable gift to charity using cash, securities, or possibly other assets. This money is then invested. In return, you become eligible to take a partial tax deduction for your donation, plus you receive a fixed stream of income from the charity for the rest of your life. At the end of your life (as well as your spouse’s, if you’re giving as a couple), the charity receives the remainder of the gift.</p>
    </div>
  </section>

</main>
</body>
</html>
```